Create a memorable Web Design for real estate branding

we are a Minnepolis brokerage and boutique housing specialist with over 27 years of experience in the Global furnished housing industry, servicing the Greater Los Angeles area. Specializing in “warm environments” we offer a customized approach to satisfying our guests and client’s needs by offering a wide array of options in highly desirable areas. Additionally, Lantern Dwelling Partners offers assistance and expertise to home buyers, sellers and investors.

Industry/Entity Type

Real Estate

Number of Pages Required

1 page

Font styles to use
Serif
Sans Serif
Decorative

```html
<!DOCTYPE html>
<html lang="en">
<head>
<meta charset="utf-8">
<title>Lantern Dwelling Partners</title>
<link href="https://fonts.googleapis.com/css2?family=Ubuntu:wght@400;500;700&family=Open+Sans:wght@400;600&display=swap" rel="stylesheet">
<style>
:root{
  --teal:#1a9a78;
  --teal-light:#3fd3a6;
  --lime:#7ab52a;
  --ink:#2b2b2b;
  --text:#555;
  --muted:#777;
  --line:#dcdcdc;
  --dark:#2a2b2e;
  --footer:#151515;
  --white:#fff;
}
*{margin:0;padding:0;box-sizing:border-box}
html,body{width:1200px;height:2368px;overflow:hidden;background:var(--white)}
body{position:relative;font-family:"Open Sans",Arial,sans-serif;color:var(--text)}
.abs{position:absolute}

/* header */
.site-header{position:absolute;left:0;top:0;width:1200px;height:98px;background:var(--white)}
.brand{position:absolute;left:133px;top:16px;font-family:"Ubuntu",sans-serif;font-weight:500;color:var(--teal);line-height:1}
.brand .brand-main{display:block;font-size:31px;letter-spacing:.5px}
.brand .brand-sub{display:block;font-size:18px;margin-top:5px;padding-left:98px;letter-spacing:1px}
.main-nav{position:absolute;right:133px;top:38px;display:flex;gap:30px;font-size:12px;color:var(--ink)}
.main-nav .active{color:var(--teal)}

/* hero */
.hero{position:absolute;left:0;top:98px;width:1200px;height:515px;
  clip-path:polygon(0 0,100% 0,100% 423px,50% 515px,0 423px);
  background:radial-gradient(ellipse at 70% 45%,#6b5a3a 0%,#2c2a3a 45%,#151a2c 100%)}
.hero-photo{position:absolute;inset:0;
  background:linear-gradient(180deg,rgba(40,50,90,.6) 0%,rgba(120,95,50,.35) 45%,rgba(25,25,30,.7) 100%)}
.hero-caption{position:absolute;left:376px;top:240px;width:445px;height:41px;background:var(--teal);
  color:var(--white);font-family:"Ubuntu",sans-serif;font-weight:500;font-size:22px;line-height:41px;text-align:center;letter-spacing:.3px}
.hero-arrow{position:absolute;top:214px;width:20px;height:24px}
.hero-arrow.prev{left:2px}.hero-arrow.next{right:2px}

/* welcome */
.welcome-title{position:absolute;left:0;top:650px;width:1200px;text-align:center;font-family:"Ubuntu",sans-serif;font-size:32px;color:var(--teal)}
.welcome-title span{color:var(--lime)}
.welcome-text{position:absolute;left:133px;top:700px;width:934px;text-align:center;font-size:10px;line-height:19px;color:var(--text)}
.btn-outline{position:absolute;left:551px;top:793px;width:98px;height:41px;border:1px solid #cfcfcf;font-size:12px;line-height:39px;text-align:center;color:var(--ink)}

/* listings */
.listings{position:absolute;left:0;top:881px;width:1200px;height:497px;
  clip-path:polygon(0 66px,50% 0,100% 66px,100% 100%,0 100%);
  background:linear-gradient(135deg,#3a3b3f 0%,#232428 40%,#303136 70%,#1e1f22 100%)}
.section-head{position:absolute;left:0;width:1200px;text-align:center;font-family:"Ubuntu",sans-serif;font-size:31px}
.listings .section-head{top:43px;color:var(--teal-light)}
.listings .section-head span{color:var(--lime)}
.head-arrow{position:absolute;top:56px;width:20px;height:14px}
.listing-card{position:absolute;top:104px;width:288px;height:344px;background:var(--white);text-align:center}
.listing-photo{width:100%;height:177px}
.listing-card h3{font-weight:400;font-size:13.5px;line-height:19px;color:var(--ink);margin:22px 18px 0}
.listing-card p{font-size:9.5px;line-height:14px;color:var(--muted);margin:10px 22px 0}
.view-more{position:absolute;left:0;bottom:22px;width:100%;font-size:9.5px;color:var(--teal);text-decoration:underline}

/* testimonials */
.testimonials{position:absolute;left:0;top:1378px;width:1200px;height:441px;
  background:linear-gradient(120deg,#e9e9e9 0%,#dcdcdc 35%,#e6e6e6 60%,#d8d8d8 100%)}
.testimonials .section-head{top:48px;font-weight:700;font-size:46px;color:#777;letter-spacing:.5px}
.avatar{position:absolute;left:557px;top:120px;width:86px;height:86px;border-radius:50%;border:3px solid #cfcfcf;background:linear-gradient(160deg,#b89a80,#6f5a4b)}
.quote{position:absolute;left:190px;top:228px;width:820px;text-align:center;font-size:21px;line-height:33px;color:#8a8a8a}
.quote .mark{font-family:"Ubuntu",sans-serif;font-weight:700;font-size:38px;color:#8a8a8a;vertical-align:-8px;line-height:0}
.quote-author{position:absolute;left:0;top:342px;width:1200px;text-align:center;font-size:16px;color:var(--ink)}
.dots{position:absolute;left:570px;top:383px;display:flex;gap:8px}
.dots i{display:block;width:8px;height:8px;border-radius:50%;background:#aaa}
.dots i.on{background:#222}

/* news */
.news-title{position:absolute;left:133px;top:1864px;font-family:"Ubuntu",sans-serif;font-size:31px;color:var(--teal)}
.news-title span{color:var(--lime)}
.pager{position:absolute;top:1873px;width:24px;height:27px;border:1px solid #ccc;background:var(--white)}
.news-card{position:absolute;top:1922px;width:296px;height:134px;border:1px solid #e0e0e0;border-top:3px solid var(--teal);background:var(--white)}
.news-date{position:absolute;left:11px;top:20px;text-align:center;color:var(--lime);font-size:11px;line-height:1}
.news-date b{display:block;font-weight:400;font-size:23px;color:var(--teal);margin-top:4px}
.news-card h4{position:absolute;left:53px;top:15px;right:10px;font-weight:400;font-size:13.5px;line-height:17px;color:var(--ink)}
.news-card p{position:absolute;left:53px;top:55px;right:12px;font-size:9.5px;line-height:14.5px;color:var(--muted);text-align:justify}

/* footer */
.site-footer{position:absolute;left:0;top:2113px;width:1200px;height:255px;background:var(--footer);color:#ccc}
.contact-label{position:absolute;left:133px;font-size:12px;color:#ddd}
.contact-value{position:absolute;left:133px;font-size:18px;color:var(--white)}
.v-rule{position:absolute;top:32px;width:1px;height:112px;background:#333}
.foot-links{position:absolute;list-style:none;font-size:11.5px;color:#aaa}
.foot-links li::before{content:"•";margin-right:7px;font-size:9px;vertical-align:1px}
.newsletter-label{position:absolute;left:842px;top:30px;font-size:11.5px;color:#ddd;letter-spacing:.2px}
.newsletter-field{position:absolute;left:842px;top:52px;width:225px;height:39px;background:#2b2b2b;font-size:11.5px;line-height:39px;padding-left:16px;color:#8a8a8a}
.social{position:absolute;top:133px;width:14px;height:14px;border-radius:50%;background:#bbb}
.foot-bar{position:absolute;left:0;top:189px;width:1200px;height:1px;background:#2a2a2a}
.foot-brand{position:absolute;left:133px;top:200px;font-family:"Ubuntu",sans-serif;font-weight:500;color:#777;line-height:1}
.foot-brand .brand-main{display:block;font-size:21px}
.foot-brand .brand-sub{display:block;font-size:12px;margin-top:3px;padding-left:66px;letter-spacing:1px}
.copyright{position:absolute;right:133px;top:215px;font-size:11px;color:#aaa}
</style>
</head>
<body>

<header class="site-header">
  <div class="brand"><span class="brand-main">Lantern Dwelling</span><span class="brand-sub">Partners</span></div>
  <nav class="main-nav"><span class="active">Home</span><span>About us</span><span>Services</span><span>Propertise</span><span>Contact us</span></nav>
</header>

<section class="hero">
  <div class="hero-photo" role="img" aria-label="Night view over a city with a light-trailed highway curving through glowing streets"></div>
  <div class="hero-caption">Specializing in “Warm Environments”</div>
  <svg class="hero-arrow prev" viewBox="0 0 20 24"><path d="M13 4 5 12l8 8" fill="none" stroke="#fff" stroke-width="2"/></svg>
  <svg class="hero-arrow next" viewBox="0 0 20 24"><path d="M7 4l8 8-8 8" fill="none" stroke="#fff" stroke-width="2"/></svg>
</section>

<h1 class="welcome-title" style="font-weight:400">Welcome to <span>Lantern Dwelling Partners</span></h1>
<p class="welcome-text">Morbi a enim eget mauris feugiat maximus. Vestibulum ante ipsum primis in faucibus orci luctus et ultrices posuere cubilia Curae; Duis bibendum felis mi, eget maximus sem consectetur id. Aenean laoreet dolor id venenatis ornare. Morbi in lacinia orci. Suspendisse at velit non leo tincidunt ultrices. Proin porta, lacus ac tempor mattis, turpis velit tempus quam, vel consectetur elit massa ac nisi. Vivamus ac elit porttitor, maximus purus in, tincidunt mi. Vestibulum ante ipsum primis in faucibus orci luctus et ultrices posuere cubilia Curae; Praesent porttitor vitae odio a vehicula. Cras tristique ullamcorper nunc, sed lacinia dui vestibulum</p>
<div class="btn-outline">Contact Us</div>

<section class="listings">
  <h2 class="section-head" style="font-weight:400">Latest <span>Listings</span></h2>
  <svg class="head-arrow" style="left:452px" viewBox="0 0 20 14"><path d="M18 7H3m5-5L3 7l5 5" fill="none" stroke="#999" stroke-width="1.6"/></svg>
  <svg class="head-arrow" style="left:730px" viewBox="0 0 20 14"><path d="M2 7h15m-5-5 5 5-5 5" fill="none" stroke="#999" stroke-width="1.6"/></svg>

  <article class="listing-card" style="left:133px">
    <div class="listing-photo" role="img" aria-label="Modern white two-storey house with palm trees" style="background:linear-gradient(160deg,#dfe3e4,#a9b0ae 60%,#5c7052)"></div>
    <h3>Suspendisse facilisis odio ut nunc pulvinar commodo nunc sed.</h3>
    <p>Nulla amet pretium tellus. Nulla in sapien vel nunc sagittis lacinia. Ut eleifend imperdiet tellus, sagittis nisi dapibus vitae. Fusce tristique lacus id pretium.</p>
    <span class="view-more">VIEW MORE</span>
  </article>
  <article class="listing-card" style="left:456px">
    <div class="listing-photo" role="img" aria-label="Lit patio with wooden deck outside a house at dusk" style="background:linear-gradient(170deg,#3c4a3a,#8a5a32 55%,#5a3a22)"></div>
    <h3>Suspendisse facilisis odio ut nunc pulvinar commodo nunc sed.</h3>
    <p>Nulla amet pretium tellus. Nulla in sapien vel nunc sagittis lacinia. Ut eleifend imperdiet tellus, sagittis nisi dapibus vitae. Fusce tristique lacus id pretium.</p>
    <span class="view-more">VIEW MORE</span>
  </article>
  <article class="listing-card" style="left:779px">
    <div class="listing-photo" role="img" aria-label="Suburban family house with garage under blue sky" style="background:linear-gradient(180deg,#2c6bd0,#8fb3d8 50%,#6a8a52)"></div>
    <h3>Suspendisse facilisis odio ut nunc pulvinar commodo nunc sed.</h3>
    <p>Nulla amet pretium tellus. Nulla in sapien vel nunc sagittis lacinia. Ut eleifend imperdiet tellus, sagittis nisi dapibus vitae. Fusce tristique lacus id pretium.</p>
    <span class="view-more">VIEW MORE</span>
  </article>
</section>

<section class="testimonials">
  <h2 class="section-head">CLIENT’S TESTIMONIALS</h2>
  <div class="avatar" role="img" aria-label="Portrait of the client"></div>
  <p class="quote"><span class="mark">“</span> Nullam sit amet consectetur magna, sed fermentum urna. Fusce varius convallis ul trices. Suspendisse sapien dui, rutrum vestibulum dui sed, tincidunt posuere purus. Morbi accumsan facilisis ligula. <span class="mark">”</span></p>
  <p class="quote-author">- Mara Ellison, City</p>
  <div class="dots"><i class="on"></i><i></i><i></i><i></i></div>
</section>

<h2 class="news-title" style="font-weight:400">Latest <span>News</span></h2>
<svg class="pager" style="left:1014px" viewBox="0 0 24 27"><path d="M14 9l-4 4.5 4 4.5" fill="none" stroke="#555" stroke-width="1.4"/></svg>
<svg class="pager" style="left:1043px" viewBox="0 0 24 27"><path d="M10 9l4 4.5-4 4.5" fill="none" stroke="#555" stroke-width="1.4"/></svg>

<article class="news-card" style="left:133px">
  <div class="news-date">May<b>14</b></div>
  <h4>Donec dolor tortor, aliquam quis nulla nec, elementum finibus</h4>
  <p>Phasellus nec sapien vitae nulla bibendum commodo. Morbi suscipit molestie dolor non aliquam. Donec id fringilla tortor. Praesent in feugiat ligula, sit amet commodo risus.</p>
</article>
<article class="news-card" style="left:452px">
  <div class="news-date">May<b>14</b></div>
  <h4>Donec dolor tortor, aliquam quis nulla nec, elementum finibus</h4>
  <p>Phasellus nec sapien vitae nulla bibendum commodo. Morbi suscipit molestie dolor non aliquam. Donec id fringilla tortor. Praesent in feugiat ligula, sit amet commodo risus.</p>
</article>
<article class="news-card" style="left:771px">
  <div class="news-date">May<b>14</b></div>
  <h4>Donec dolor tortor, aliquam quis nulla nec, elementum finibus</h4>
  <p>Phasellus nec sapien vitae nulla bibendum commodo. Morbi suscipit molestie dolor non aliquam. Donec id fringilla tortor. Praesent in feugiat ligula, sit amet commodo risus.</p>
</article>

<footer class="site-footer">
  <span class="contact-label" style="top:30px">Email</span>
  <span class="contact-value" style="top:45px">info@lanterndwelling.com</span>
  <span class="contact-label" style="top:91px">Call us on</span>
  <span class="contact-value" style="top:107px">555 014 2290</span>
  <div class="v-rule" style="left:365px"></div>
  <ul class="foot-links" style="left:426px;top:27px;line-height:29px">
    <li>Home</li><li>About us</li><li>Services</li><li>Propertise</li><li>Contact us</li>
  </ul>
  <ul class="foot-links" style="left:617px;top:27px;line-height:37px">
    <li>Privacy Policy</li><li>Terms and conditions</li><li>Sitemap</li>
  </ul>
  <div class="v-rule" style="left:796px"></div>
  <span class="newsletter-label">NEWSLETTER SUBSCRIBE</span>
  <div class="newsletter-field">Email Address</div>
  <svg class="abs" style="left:1036px;top:65px" width="16" height="12" viewBox="0 0 16 12"><rect x=".75" y=".75" width="14.5" height="10.5" fill="none" stroke="#bbb" stroke-width="1.3"/><path d="M1 1l7 6 7-6" fill="none" stroke="#bbb" stroke-width="1.3"/></svg>
  <i class="social" style="left:839px"></i><i class="social" style="left:877px"></i><i class="social" style="left:915px"></i><i class="social" style="left:955px"></i>
  <div class="foot-bar"></div>
  <div class="foot-brand"><span class="brand-main">Lantern Dwelling</span><span class="brand-sub">Partners</span></div>
  <span class="copyright">Copyright © 2016 Northfield Studio.&nbsp;&nbsp;All rights reserved.</span>
</footer>

</body>
</html>
```